Business card design for new eCommerce site focusing on integrity and strong businsess tactics

We need a business card that will stand out and be memorable. Something with color that matches our company logo colors. Think high end version of Pactivo. There are 2 logos provided. The parent company is called Amber Ledge Partners and we are presenting a new and very exciting eCommerce site called BrightHarborTrade.example.

Target Market(s)

Our target markets are in the Activities, Food and Beverage, Health and Beauty

Industry/Entity Type

Marketing

Contact Information for Business Card

We have 4 members that need cards...I will provide all info to the winner of the design contest
Business Address is
4870 West 63rd Avenue, Suite C207
Phoenix AZ 85731

Font styles to use
Serif
Sans Serif

Colors

Designer to choose colors to be used in the design.

Requirements
Must have
• The card must be memorable...should be unique in design but must exude integrity and be playful .
• I have provided several colors or our parent company...please feel free to use which ever
Nice to have
• I will leave this up to you. Feel free to use other images of your choosing that wraps around our client.....Activities, Dining, Health, Beauty
Should not have
• just dont be boring

```html
<!DOCTYPE html>
<html lang="en">
<head>
<meta charset="utf-8">
<title>BrightHarborTrade.example business card</title>
<link rel="stylesheet" href="https://fonts.googleapis.com/css2?family=Open+Sans:wght@400;600;700&family=Arimo:wght@700&display=swap">
<style>
  :root {
    --backdrop: #2a2a2a;
    --paper: #f2f2f2;
    --harbor-blue: #2c77aa;
    --leaf-green: #77b82e;
    --lime: #a6c94a;
    --ink-grey: #6f6f6f;
    --white: #ffffff;
  }
  * { margin: 0; padding: 0; box-sizing: border-box; }
  html, body { width: 1200px; height: 960px; overflow: hidden; }
  body {
    background: var(--backdrop);
    font-family: "Open Sans", Arial, sans-serif;
    position: relative;
  }
  .card {
    position: absolute;
    width: 600px;
    height: 343px;
    background: var(--paper);
    overflow: hidden;
  }
  .card--front { left: 314px; top: 113px; }
  .card--back { left: 311px; top: 472px; }

  .brand {
    position: absolute;
    left: 36px;
    top: 70px;
  }
  .brand__name {
    font-weight: 700;
    font-size: 19px;
    color: var(--leaf-green);
    line-height: 1.1;
  }
  .brand__tagline {
    margin-top: 4px;
    font-size: 11px;
    letter-spacing: 0.4px;
    color: var(--ink-grey);
  }

  .holder {
    position: absolute;
    right: 38px;
    top: 64px;
    text-align: right;
  }
  .holder__name {
    font-weight: 700;
    font-size: 20px;
    color: var(--harbor-blue);
    letter-spacing: 0.3px;
    line-height: 1.2;
  }
  .holder__role {
    font-size: 14px;
    color: var(--leaf-green);
    line-height: 1.2;
  }

  .contact-band {
    position: absolute;
    left: 0;
    top: 180px;
    width: 600px;
    height: 163px;
    background: var(--harbor-blue);
  }
  .contact-band__accent {
    position: absolute;
    left: 0;
    top: 0;
  }
  .contact {
    position: absolute;
    left: 36px;
    top: 20px;
    color: var(--white);
    font-size: 14px;
    line-height: 19px;
  }
  .contact__address { margin-bottom: 8px; }
  .contact__list { list-style: none; }
  .contact__item { display: flex; align-items: center; gap: 8px; }
  .contact__icon { width: 14px; height: 14px; flex: none; }

  .parent-mark {
    position: absolute;
    left: 0;
    width: 600px;
    top: 70px;
    text-align: center;
  }
  .parent-mark__circle {
    display: block;
    margin: 0 auto;
    width: 146px;
    height: 146px;
    border-radius: 50%;
    background: var(--lime);
  }
  .parent-mark__name {
    margin-top: 12px;
    font-family: "Arimo", Arial, sans-serif;
    font-weight: 700;
    font-size: 34px;
    color: var(--lime);
    line-height: 1;
  }
</style>
</head>
<body>

  <section class="card card--front">
    <div class="brand">
      <div class="brand__name">BrightHarborTrade.example</div>
      <div class="brand__tagline">Activities-Dining-Health-Beauty</div>
    </div>

    <div class="holder">
      <div class="holder__name">DANIEL REYES</div>
      <div class="holder__role">CEO/FOUNDER</div>
    </div>

    <div class="contact-band">
      <svg class="contact-band__accent" width="600" height="163" viewBox="0 0 600 163">
        <path d="M410 0 L600 0 L600 163 L505 163 C470 120 418 62 410 0 Z" fill="var(--leaf-green)"/>
      </svg>

      <div class="contact">
        <div class="contact__address">4870 West 63rd Avenue<br>Suite C207, Phoenix AZ 85731</div>
        <ul class="contact__list">
          <li class="contact__item">
            <svg class="contact__icon" viewBox="0 0 16 16"><path d="M4 1 L6.5 4 L5 6 C6 8 8 10 10 11 L12 9.5 L15 12 L13 15 C7 14 2 9 1 3 Z" fill="var(--white)"/></svg>
            602 555 0148
          </li>
          <li class="contact__item">
            <svg class="contact__icon" viewBox="0 0 16 16"><rect x="4" y="1" width="8" height="14" rx="1.5" fill="none" stroke="var(--white)" stroke-width="1.8"/><circle cx="8" cy="12.3" r="0.9" fill="var(--white)"/></svg>
            602 555 0193
          </li>
          <li class="contact__item">
            <svg class="contact__icon" viewBox="0 0 16 16"><rect x="1.5" y="4" width="13" height="9" fill="var(--white)"/><path d="M1.5 4 L8 9 L14.5 4" fill="none" stroke="var(--harbor-blue)" stroke-width="1.2"/></svg>
            daniel@brightharbortrade.example
          </li>
          <li class="contact__item">
            <svg class="contact__icon" viewBox="0 0 16 16"><circle cx="8" cy="8" r="6.5" fill="var(--white)"/><path d="M1.5 8 H14.5 M8 1.5 C5 5 5 11 8 14.5 M8 1.5 C11 5 11 11 8 14.5" fill="none" stroke="var(--harbor-blue)" stroke-width="1"/></svg>
            www.brightharbortrade.example
          </li>
        </ul>
      </div>
    </div>
  </section>

  <section class="card card--back">
    <div class="parent-mark">
      <span class="parent-mark__circle"></span>
      <div class="parent-mark__name">Amber Ledge Partners</div>
    </div>
  </section>

</body>
</html>
```